Lorvex Tilo medical cannibis cultivation company

tag - Tilo rise
Lorvex Tilo medical cannabis cultivation - logo is selected- can we please see bold examples with our selection. We are mainly dealing with medical companies and professionals. We would like to be stand out in the crowd with our designs. Welcome any and all attempts. Thanks

Target Market(s)

Medical and Professional

Industry/Entity Type

Medical And Science

Font styles to use
Sans Serif

Colors

Designer to choose colors to be used in the design.

Requirements
Must have
• Bright colour and be bold- Love the teal and magenta that is currently on the dark background design.
Nice to have
• shading and the 3D affect- The shadowed appearance.
Should not have
• Anything related to illegal activity or un professional manners

```html
<!DOCTYPE html>
<html lang="en">
<head>
<meta charset="utf-8">
<title>Lorvex Tilo Stationery</title>
<link href="https://fonts.googleapis.com/css2?family=Questrial&family=Roboto:wght@400;700&display=swap" rel="stylesheet">
<style>
:root{
  --stage:#dcdcdc;
  --paper:#f6f6f6;
  --sky:#00aee8;
  --plum:#9e4f9b;
  --ink:#444;
  --ring:#8a8a8a;
  --flap:#000;
  --white:#fff;
}
*{box-sizing:border-box;margin:0;padding:0}
html,body{width:1200px;height:877px;overflow:hidden;background:var(--stage)}
.canvas{position:relative;width:1200px;height:877px}
.sheet{position:absolute;background:var(--paper);overflow:hidden}
.band-top{position:absolute;left:0;top:0;width:100%;background:var(--sky)}
.band-foot{position:absolute;left:0;bottom:0;width:100%;background:var(--plum);color:var(--white);
  font-family:"Roboto",sans-serif;font-size:8.6px;line-height:11px;text-align:center;padding-top:12px}
.band-foot b{font-weight:700}
.emblem{position:absolute;width:60px;height:60px;border-radius:50%;background:var(--white);border:2px solid var(--ring)}
.brand{position:absolute;text-align:center;font-family:"Questrial",sans-serif}
.brand-name{font-size:17px;line-height:17px;color:var(--sky);letter-spacing:.3px}
.brand-tag{display:flex;align-items:center;gap:3px;justify-content:center;font-size:6.5px;color:#777;letter-spacing:1px;margin-top:1px}
.brand-tag::before,.brand-tag::after{content:"";display:block;width:20px;height:1px;background:#888}

/* letterhead */
.letterhead{left:61px;top:66px;width:527px;height:742px}
.letterhead .band-top{height:77px}
.letterhead .band-foot{height:46px}
.letter{position:absolute;left:46px;top:206px;width:439px;font-family:"Questrial",sans-serif;color:var(--ink)}
.salutation{font-size:13.5px;margin-bottom:22px}
.letter p{font-size:7.6px;line-height:11.4px;text-align:justify;margin-bottom:11.4px}
.closing{margin-top:20px;font-size:7.6px}
.signature{position:absolute;left:41px;top:518px;width:94px;height:38px;background:linear-gradient(90deg,rgba(30,60,160,.12),rgba(30,60,160,.05));border-radius:4px}

/* envelope back */
.envelope-back{left:615px;top:299px;width:531px;height:240px}
.flap{position:absolute;left:0;top:0;width:100%;height:74px;background:var(--flap);border-radius:0 0 26px 26px}
.flap-mark{position:absolute;left:50%;top:39px;transform:translate(-50%,-50%);display:flex;align-items:center;gap:5px;
  font-family:"Questrial",sans-serif;font-size:9px;color:var(--white)}
.flap-mark i{display:block;width:14px;height:14px;border-radius:50%;border:1.5px solid var(--ring)}

/* envelope front */
.envelope-front{left:615px;top:568px;width:531px;height:239px}
.envelope-front .band-top{height:66px}
.envelope-front .band-foot{height:45px;padding-top:12px}
</style>
</head>
<body>
<div class="canvas">

  <section class="sheet letterhead">
    <div class="band-top"></div>
    <div class="emblem" style="left:234px;top:42px"></div>
    <div class="brand" style="left:199px;top:96px;width:130px">
      <div class="brand-name">LORVEX TILO</div>
      <div class="brand-tag">TILO RISE</div>
    </div>

    <div class="letter">
      <div class="salutation">Dear Mr. Harlow,</div>
      <p>Lorem ipsum dolor sit amet, consectetur adipiscing elit. Donec orci purus, luctus vitae dignissim eu, iaculis sed purus. Vivamus faucibus, ipsum nec aliquet viverra, leo mauris condimentum ligula, sit amet sagittis enim ligula quis arcu. Nam egestas tortor id nisi porttitor mattis. In tortor ante, ultricies in suscipit a, tempus non massa. Vivamus et auctor mi. Fusce vel massa nulla. Phasellus nec eros mauris, et scelerisque orci.</p>
      <p>Donec malesuada orci vitae nulla accumsan porta a id massa. Quisque accumsan iaculis magna sit amet fringilla. Maecenas consequat, magna eget tincidunt semper, odio nibh rutrum mi, id feugiat ante nisi eu risus. Vestibulum nunc orci, rhoncus a placerat in, ultricies in mi. Cras mattis varius eros, vel fringilla nisi suscipit eget. Quisque scelerisque sagittis nulla at porttitor.</p>
      <p>Sed id augue vitae urna euismod commodo aliquet a quam. Pellentesque arcu velit, cursus et malesuada ut, consequat et diam. Nullam erat sem, rhoncus id ullamcorper vitae, rhoncus et arcu. In ultricies ultricies nulla, ut rutrum nisi iaculis at. Donec eu magna a metus ornare faucibus. Fusce aliquet faucibus ultricies. Morbi semper, est id tincidunt gravida, sem arcu adipiscing lacus, ac bibendum nulla leo eu purus. Quisque nec diam sed risus consectetur accumsan quis quis nibh. Vestibulum id purus lorem.</p>
      <p>It is a long established fact that a reader will be distracted by the readable content of a page when looking at its layout. The point of using Lorem Ipsum is that it has a more-or-less normal distribution of letters, as opposed to using 'Content here, content here', making it look like readable English. Many desktop publishing packages</p>
      <div class="closing">Sincerely,</div>
    </div>
    <div class="signature" role="img" aria-label="Handwritten signature of Kai Harlow"></div>

    <footer class="band-foot">
      2140 Wrenfield Road, Calder Bay, Ontario 55812 &nbsp;|&nbsp; <b>P:</b> 555 210 4417<br>
      <b>C:</b> 555 318 7702 <b>F:</b> 555 604 2291 <b>E:</b> kai@lorvextilo.com &nbsp;<b>W:</b> www.lorvextilo.com
    </footer>
  </section>

  <section class="sheet envelope-back">
    <div class="flap">
      <div class="flap-mark"><i></i>Lorvex Tilo</div>
    </div>
  </section>

  <section class="sheet envelope-front">
    <div class="band-top"></div>
    <div class="emblem" style="left:64px;top:26px"></div>
    <div class="brand" style="left:29px;top:80px;width:130px">
      <div class="brand-name">LORVEX TILO</div>
      <div class="brand-tag">TILO RISE</div>
    </div>
    <footer class="band-foot">
      2140 Wrenfield Road, Calder Bay, Ontario 55812 &nbsp;|&nbsp; <b>P:</b> 555 210 4417<br>
      <b>C:</b> 555 318 7702 <b>F:</b> 555 604 2291 <b>E:</b> kai@lorvextilo.com &nbsp;<b>W:</b> www.lorvextilo.com
    </footer>
  </section>

</div>
</body>
</html>
```